Create a new dynamic Video Production company website

A new website for a video production company. It needs to be focused on the videos with an easy to use and versatile video player. I want to be able to update (add/remove/edit) the videos myself and change some other regular information like price lists. Current website is www.reelvanta.ca
The new pages will be - Home - Corporate - Ministry - Wedding - Events - Contact

I was asked about Wordpress - I am not against WordPress so long as the designing company sets everything up properly. I have had bad experiences with Wordpress security (and spam) so as long as those issues are addressed, I can work with Wordpress.

Coding

Coded - Design and coding required

Number of Pages Required

5+ page

Requirements
Must have
• Video player that scales to different platforms - computers, tablets, cell phones etc.

```html
<!DOCTYPE html>
<html lang="en">
<head>
<meta charset="utf-8">
<title>Reelvanta — Video Production</title>
<link rel="stylesheet" href="https://fonts.googleapis.com/css2?family=Mulish:wght@400;600;700&display=swap">
<style>
  :root{
    --ink:#1f1b1c;
    --ink-soft:#2f2a2b;
    --text:#3a3a3a;
    --muted:#8a8a8a;
    --hero-bg:#e9e8e7;
    --white:#ffffff;
    --band-dark:#3d3c3d;
    --band-light:#a9a9a9;
    --card-top:#a3a3a3;
    --card-top-light:#c9c9c9;
    --footer:#232021;
    --footer-text:#d6d6d6;
  }
  *{box-sizing:border-box;margin:0;padding:0}
  html,body{width:1200px;height:2416px;overflow:hidden;background:var(--white)}
  body{position:relative;font-family:"Mulish",Arial,sans-serif;color:var(--text)}
  .abs{position:absolute}

  /* Header + hero */
  .hero{left:0;top:0;width:1200px;height:657px;
    background:linear-gradient(100deg,#efeeed 0%,#e6e5e4 55%,#cfcdcc 80%,#bdbbba 100%)}
  .hero-scene{left:0;top:0;width:1200px;height:657px;
    background:radial-gradient(ellipse 260px 360px at 1080px 260px,rgba(90,88,88,.35),rgba(90,88,88,0) 70%)}
  .brand{left:113px;top:34px;font-size:44px;font-weight:700;letter-spacing:2px;color:var(--ink);display:flex;align-items:center;gap:14px}
  .brand-dot{width:30px;height:30px;border-radius:50%;background:var(--ink)}
  .main-nav{left:495px;top:58px;display:flex;gap:30px;font-size:16px;font-weight:600;color:var(--ink)}
  .main-nav a{color:inherit;text-decoration:none;position:relative}
  .main-nav a.is-active::after{content:"";position:absolute;left:0;right:0;top:28px;height:2px;background:var(--ink)}

  .player{left:267px;top:174px;width:651px;height:390px;background:var(--ink);box-shadow:0 6px 18px rgba(0,0,0,.35)}
  .player-screen{left:0;top:0;width:651px;height:338px;
    background:linear-gradient(90deg,#8a5b34 0%,#a5774a 30%,#6f7d52 60%,#8c9a6b 100%)}
  .player-progress{left:0;top:333px;width:651px;height:5px;background:rgba(255,255,255,.25)}
  .player-progress-fill{left:0;top:333px;width:36px;height:5px;background:var(--white)}
  .player-knob{left:26px;top:325px;width:20px;height:20px;border-radius:50%;background:var(--white)}
  .player-big-play{left:283px;top:132px}
  .player-controls{left:240px;top:352px}
  .slider-arrow{width:52px;height:52px}

  /* Welcome */
  .welcome{left:0;top:657px;width:1200px;height:487px;background:var(--white)}
  .welcome-photo{left:693px;top:657px;width:507px;height:487px;
    background:linear-gradient(90deg,rgba(255,255,255,1) 0%,rgba(250,200,150,.7) 18%,#e58a3a 32%,#3b3635 55%,#1e1c1c 100%)}
  .welcome-play{left:818px;top:863px}
  .welcome-title{left:120px;top:764px;font-size:35px;font-weight:600;color:var(--ink);letter-spacing:.5px}
  .welcome-copy{left:122px;top:830px;width:440px;font-size:13.5px;line-height:22px;color:#8d8d8d}
  .welcome-copy p+p{margin-top:10px}
  .btn-dark{display:flex;align-items:center;justify-content:center;background:var(--ink-soft);color:var(--white);font-size:14px;font-weight:600;letter-spacing:.5px}
  .welcome-btn{left:122px;top:1000px;width:168px;height:44px}

  /* Services */
  .services{left:0;top:1144px;width:1200px;height:465px;
    background:linear-gradient(160deg,#2e2d2e 0%,#4a494a 35%,#7a797a 70%,#a8a8a8 100%)}
  .service{width:220px;text-align:center;color:var(--white)}
  .service-icon{display:block;margin:0 auto}
  .service-title{margin-top:14px;font-size:19px;font-weight:600;letter-spacing:.5px}
  .service-copy{margin-top:8px;font-size:12px;line-height:18px;color:#cfcfcf}
  .service-btn{display:inline-flex;align-items:center;justify-content:center;margin-top:20px;width:112px;height:32px;border:2px solid var(--white);font-size:14px;color:var(--white)}

  /* Pricing */
  .pricing-title{left:0;top:1662px;width:1200px;text-align:center;font-size:28px;font-weight:600;color:var(--ink-soft);letter-spacing:1px}
  .plan{top:1729px;width:303px;height:427px;background:var(--white);box-shadow:0 2px 10px rgba(0,0,0,.22)}
  .plan-head{left:0;top:0;width:303px;height:165px;background:linear-gradient(180deg,var(--card-top) 0%,var(--card-top-light) 100%)}
  .plan--premium .plan-head{background:linear-gradient(180deg,#8c8c8c 0%,#b8b8b8 100%)}
  .plan-wave{left:0;top:120px}
  .plan-name{left:0;top:30px;width:303px;text-align:center;font-size:22px;color:var(--white)}
  .plan-price{left:0;top:56px;width:303px;text-align:center;font-size:44px;font-weight:600;color:var(--white)}
  .plan-price small{font-size:28px}
  .plan-list{left:60px;top:184px;list-style:none;font-size:14px;color:#555}
  .plan-list li{height:33px;line-height:33px;padding-left:16px;position:relative}
  .plan-list li::before{content:"";position:absolute;left:0;top:13px;width:5px;height:5px;border-right:1.5px solid #555;border-top:1.5px solid #555;transform:rotate(45deg)}
  .plan-btn{left:81px;top:404px;width:140px;height:36px;background:var(--ink);font-size:14px}

  /* Footer */
  .footer{left:0;top:2260px;width:1200px;height:156px;background:var(--footer)}
  .footer-nav{left:139px;top:2298px;display:flex;gap:26px;font-size:15.5px;font-weight:600;color:var(--white)}
  .footer-copy{left:139px;top:2333px;font-size:13px;color:#9a9a9a}
  .footer-social{left:953px;top:2301px;display:flex;gap:8px}
  .footer-social span{width:30px;height:30px;border:1.5px solid var(--white);border-radius:50%}
</style>
</head>
<body>

  <!-- Hero -->
  <div class="abs hero" role="img" aria-label="Soft grey backdrop of a film crew on set"></div>
  <div class="abs hero-scene"></div>

  <div class="abs brand"><span class="brand-dot"></span>REELVANTA</div>
  <nav class="abs main-nav">
    <a class="is-active">HOME</a><a>CORPORATE</a><a>MINISTRY</a><a>WEDDING</a><a>EVENTS</a><a>CONTACT</a>
  </nav>

  <svg class="abs slider-arrow" style="left:108px;top:333px" viewBox="0 0 52 52"><circle cx="26" cy="26" r="24" fill="#fff" stroke="#1f1b1c" stroke-width="2"/><path d="M30 16 L20 26 L30 36" fill="none" stroke="#1f1b1c" stroke-width="3"/></svg>
  <svg class="abs slider-arrow" style="left:1057px;top:333px" viewBox="0 0 52 52"><circle cx="26" cy="26" r="24" fill="#fff" stroke="#1f1b1c" stroke-width="2"/><path d="M22 16 L32 26 L22 36" fill="none" stroke="#1f1b1c" stroke-width="3"/></svg>

  <div class="abs player">
    <div class="abs player-screen" role="img" aria-label="Video still of a wedding couple beside a wooden chapel"></div>
    <svg class="abs player-big-play" width="100" height="100" viewBox="0 0 100 100"><circle cx="50" cy="50" r="47" fill="rgba(0,0,0,.08)" stroke="#fff" stroke-width="4"/><path d="M40 32 L68 50 L40 68 Z" fill="none" stroke="#fff" stroke-width="4" stroke-linejoin="round"/></svg>
    <div class="abs player-progress"></div>
    <div class="abs player-progress-fill"></div>
    <div class="abs player-knob"></div>
    <svg class="abs player-controls" width="180" height="30" viewBox="0 0 180 30">
      <path d="M40 4 L22 15 L40 26 Z M22 4 L4 15 L22 26 Z" fill="#fff"/>
      <path d="M83 4 L101 15 L83 26 Z" fill="#fff"/>
      <path d="M140 4 L158 15 L140 26 Z M158 4 L176 15 L158 26 Z" fill="#fff"/>
    </svg>
  </div>

  <!-- Welcome -->
  <section class="abs welcome"></section>
  <div class="abs welcome-photo" role="img" aria-label="Camera operator filming with a professional video camera"></div>
  <svg class="abs welcome-play" width="66" height="66" viewBox="0 0 66 66"><circle cx="33" cy="33" r="33" fill="#fff"/><path d="M26 20 L47 33 L26 46 Z" fill="#1f1b1c"/></svg>
  <h1 class="abs welcome-title">WELCOME TO REELVANTA</h1>
  <div class="abs welcome-copy">
    <p>Fusce ultricies orci ac feugiat suscipit leo massa sodales velit et sceleris-que mi tortor at ipsum cligula augue bibendum</p>
    <p>congue augue et malesuada iaculis ipsum dui aliquet felis at cursus magna nisl nec elit Praesent elementum elit at tellus nec ultricies sit amet porttitor mattis enim In massa libero interdum nec interdum vel blandit sed nulla In ullamcorper est eget tempor</p>
  </div>
  <div class="abs btn-dark welcome-btn">LEARN MORE</div>

  <!-- Services -->
  <section class="abs services"></section>
  <div class="abs service" style="left:115px;top:1233px">
    <svg class="service-icon" width="160" height="160" viewBox="0 0 160 160" role="img" aria-label="Corporate service icon"><circle cx="80" cy="80" r="70" fill="none" stroke="#d9d9d9" stroke-width="10"/></svg>
    <div class="service-title">CORPORATE</div>
    <div class="service-copy">Class aptent taciti sociosqu ad litora torquent per conubia nostra</div>
    <div class="service-btn">Click here</div>
  </div>
  <div class="abs service" style="left:359px;top:1233px">
    <svg class="service-icon" width="160" height="160" viewBox="0 0 160 160" role="img" aria-label="Ministry service icon"><circle cx="80" cy="80" r="70" fill="none" stroke="#d9d9d9" stroke-width="10"/></svg>
    <div class="service-title">MINISTRY</div>
    <div class="service-copy">Class aptent taciti sociosqu ad litora torquent per conubia nostra</div>
    <div class="service-btn">Click here</div>
  </div>
  <div class="abs service" style="left:601px;top:1233px">
    <svg class="service-icon" width="160" height="160" viewBox="0 0 160 160" role="img" aria-label="Wedding service icon"><circle cx="80" cy="80" r="70" fill="none" stroke="#d9d9d9" stroke-width="10"/></svg>
    <div class="service-title">WEDDING</div>
    <div class="service-copy">Class aptent taciti sociosqu ad litora torquent per conubia nostra</div>
    <div class="service-btn">Click here</div>
  </div>
  <div class="abs service" style="left:844px;top:1233px">
    <svg class="service-icon" width="160" height="160" viewBox="0 0 160 160" role="img" aria-label="Events service icon"><circle cx="80" cy="80" r="70" fill="none" stroke="#d9d9d9" stroke-width="10"/></svg>
    <div class="service-title">EVENTS</div>
    <div class="service-copy">Class aptent taciti sociosqu ad litora torquent per conubia nostra</div>
    <div class="service-btn">Click here</div>
  </div>

  <!-- Pricing -->
  <h2 class="abs pricing-title">OUR PRICING</h2>

  <div class="abs plan" style="left:124px">
    <div class="abs plan-head"></div>
    <svg class="abs plan-wave" width="303" height="50" viewBox="0 0 303 50" preserveAspectRatio="none"><path d="M0 30 C70 10 120 5 180 20 C230 32 270 28 303 18 L303 50 L0 50 Z" fill="#e2e2e2"/><path d="M0 40 C80 20 140 18 200 32 C250 42 280 38 303 30 L303 50 L0 50 Z" fill="#fff"/></svg>
    <div class="abs plan-name">Silver</div>
    <div class="abs plan-price"><small>$</small>49</div>
    <ul class="abs plan-list"><li>Aetus et malesuada</li><li>Games ac turpis egestas</li><li>Cras id elit Integer</li><li>Puis urna Ut ante</li><li>Enim dapibus malesuada</li><li>Felis viverrami</li></ul>
    <div class="abs btn-dark plan-btn">CLICK HERE</div>
  </div>
  <div class="abs plan" style="left:449px">
    <div class="abs plan-head"></div>
    <svg class="abs plan-wave" width="303" height="50" viewBox="0 0 303 50" preserveAspectRatio="none"><path d="M0 30 C70 10 120 5 180 20 C230 32 270 28 303 18 L303 50 L0 50 Z" fill="#e2e2e2"/><path d="M0 40 C80 20 140 18 200 32 C250 42 280 38 303 30 L303 50 L0 50 Z" fill="#fff"/></svg>
    <div class="abs plan-name">Platinium</div>
    <div class="abs plan-price"><small>$</small>79</div>
    <ul class="abs plan-list"><li>Aetus et malesuada</li><li>Games ac turpis egestas</li><li>Cras id elit Integer</li><li>Puis urna Ut ante</li><li>Enim dapibus malesuada</li><li>Felis viverrami</li></ul>
    <div class="abs btn-dark plan-btn">CLICK HERE</div>
  </div>
  <div class="abs plan plan--premium" style="left:775px">
    <div class="abs plan-head"></div>
    <svg class="abs plan-wave" width="303" height="50" viewBox="0 0 303 50" preserveAspectRatio="none"><path d="M0 30 C70 10 120 5 180 20 C230 32 270 28 303 18 L303 50 L0 50 Z" fill="#e2e2e2"/><path d="M0 40 C80 20 140 18 200 32 C250 42 280 38 303 30 L303 50 L0 50 Z" fill="#fff"/></svg>
    <div class="abs plan-name">Premium</div>
    <div class="abs plan-price"><small>$</small>99</div>
    <ul class="abs plan-list"><li>Aetus et malesuada</li><li>Games ac turpis egestas</li><li>Cras id elit Integer</li><li>Puis urna Ut ante</li><li>Enim dapibus malesuada</li><li>Felis viverrami</li></ul>
    <div class="abs btn-dark plan-btn">CLICK HERE</div>
  </div>

  <!-- Footer -->
  <footer class="abs footer"></footer>
  <nav class="abs footer-nav"><span>HOME</span><span>CORPORATE</span><span>MINISTRY</span><span>WEDDING</span><span>EVENTS</span><span>CONTACT</span></nav>
  <div class="abs footer-copy">© 2017 Company Name&nbsp; All right reserved</div>
  <div class="abs footer-social" aria-label="Social links"><span></span><span></span><span></span><span></span></div>

</body>
</html>
```